KLR Buildworks - Civil Construction Construction Company (Telecommunications)

Need a basic website to refine our branding to a current reflection of our service offerings. KLR Buildworks provides civil construction services specializing in telecommunication sector.
I have started to create a website using word press. I would like to have someone refine the design and polish the overall look and functionality of the site. I would like to website to function in the wordpress format to allow for future edits and control of site.
Included site preview:
https://pvhosts-ua.pagemakerbench.example/7e2d94fa.com/Admin/index.html/qm_draft_view

```html
<!DOCTYPE html>
<html lang="en">
<head>
<meta charset="utf-8">
<title>KLR Buildworks</title>
<link rel="stylesheet" href="https://fonts.googleapis.com/css2?family=Oswald:wght@400;700&family=Roboto:ital,wght@0,400;0,500;0,700;1,400&display=swap">
<style>
:root{
  --red:#e30613;
  --red-dark:#c8101b;
  --ink:#1b1b1b;
  --text:#4a4a4a;
  --light:#f2f3f5;
  --night:#0f0f10;
  --white:#ffffff;
}
*{margin:0;padding:0;box-sizing:border-box}
html,body{width:1200px;height:4354px;overflow:hidden}
body{position:relative;font-family:"Roboto",sans-serif;color:var(--ink);background:var(--white)}
.abs{position:absolute}
.oswald{font-family:"Oswald",sans-serif}
.brand{font-family:"Oswald",sans-serif;font-weight:400;font-size:36px;letter-spacing:1px;color:var(--ink);display:flex;align-items:center;gap:12px}
.brand-square{width:18px;height:18px;background:var(--red)}
.round{border-radius:50%}
/* header */
.site-header{top:0;left:0;width:1200px;height:77px;background:var(--white)}
.header-phone{left:660px;top:13px;display:flex;align-items:center;gap:14px;font-size:16px;font-weight:500}
.header-phone .ico{width:46px;height:46px;background:var(--red);display:flex;align-items:center;justify-content:center}
.header-divider{left:873px;top:18px;width:1px;height:40px;background:#ccc}
.header-social{left:889px;top:12px;display:flex;gap:6px}
.header-social span{width:46px;height:46px;background:var(--red);display:block}
.main-nav{top:77px;left:0;width:1200px;height:48px;background:var(--red)}
.main-nav a{position:absolute;top:15px;color:var(--white);text-decoration:none;font-size:16px;font-weight:500}
.main-nav a.current{text-decoration:underline;text-underline-offset:4px}
/* hero */
.hero{top:125px;left:0;width:1200px;height:630px;overflow:hidden}
.hero-photo{position:absolute;inset:0;background:linear-gradient(100deg,#2f4a24 0%,#4d5e2b 30%,#b58d1f 55%,#4f7a2c 80%,#a8261c 100%)}
.hero-shade{position:absolute;inset:0;background:linear-gradient(90deg,rgba(0,0,0,.45),rgba(0,0,0,0) 55%)}
.hero-title{left:110px;top:180px;font-size:58px;color:var(--white);font-weight:400}
.hero-title b{font-weight:700}
.hero-sub{left:112px;top:253px;font-size:14px;line-height:24px;color:var(--white);font-weight:500}
.btn-red{background:var(--red);color:var(--white);font-weight:500;font-size:16px;display:flex;align-items:center;justify-content:center;letter-spacing:.3px}
.hero-btn{left:112px;top:322px;width:164px;height:46px}
.hero-scroll{left:592px;top:538px;width:16px;height:26px;border:2px solid #fff;border-radius:9px}
/* about */
.about-photo{left:120px;top:817px;width:460px;height:508px;background:linear-gradient(150deg,#6b8a5a,#8a2f28 45%,#5c1c18 70%,#3f4a35);box-shadow:0 6px 20px rgba(0,0,0,.25);border:5px solid #fff}
.section-title{font-family:"Oswald",sans-serif;font-size:46px;font-weight:400;text-transform:uppercase;color:var(--ink)}
.section-title b{font-weight:700}
.about-title{left:650px;top:835px}
.about-rule{left:650px;top:897px;width:68px;height:4px;background:var(--red)}
.about-text{left:650px;top:918px;width:440px;font-size:13.5px;line-height:28.3px;color:var(--text)}
.about-btn{left:650px;top:1250px;width:166px;height:45px}
/* why */
.why{top:1410px;left:0;width:1200px;height:530px;background:linear-gradient(180deg,#1d2230,#15171c 50%,#231c14)}
.why-title{left:0;width:1200px;text-align:center;top:1478px;color:var(--white)}
.why-card{top:1576px;width:313px;height:277px;border:2px solid var(--red)}
.why-card svg{position:absolute;left:26px;top:44px}
.why-card ul{position:absolute;left:34px;top:140px;list-style:none;font-family:"Oswald",sans-serif;font-size:15px;line-height:24px;color:var(--white);width:270px}
.why-card li{position:relative;padding-left:12px}
.why-card li::before{content:"";position:absolute;left:0;top:10px;width:5px;height:5px;border-radius:50%;background:var(--red)}
/* testimonials */
.reviews{top:1940px;left:0;width:1200px;height:550px;background:var(--light)}
.reviews-title{left:0;width:1200px;text-align:center;top:2000px;font-size:36px}
.review-card{top:2078px;width:465px;height:229px;background:var(--white);box-shadow:0 4px 16px rgba(0,0,0,.06)}
.review-card .tail{position:absolute;left:45px;bottom:-18px;width:0;height:0;border-left:0 solid transparent;border-right:40px solid transparent;border-top:18px solid var(--white)}
.review-card .quote{position:absolute;left:26px;top:20px;font-family:"Oswald",sans-serif;font-size:48px;line-height:48px;color:var(--red);font-weight:700}
.review-card .stars{position:absolute;left:76px;top:26px;color:#f5b400;font-size:20px;letter-spacing:2px}
.review-card p{position:absolute;left:26px;top:66px;width:420px;font-style:italic;font-size:16px;line-height:32px;color:#333}
.avatar{top:2342px;width:60px;height:60px;background:linear-gradient(160deg,#9aa3ad,#4c545c)}
.reviewer{top:2348px;font-size:18px;font-weight:700}
.reviewer small{display:block;font-size:13px;font-weight:400;color:#555;margin-top:6px}
.arrow{top:2172px}
/* work */
.work-title{left:0;width:1200px;text-align:center;top:2560px}
.work-tile{width:316px;height:326px}
/* contact */
.contact{top:3398px;left:0;width:1200px;height:575px;background:linear-gradient(135deg,#e3121d,#d0101a 50%,#e4222a)}
.contact-title{left:0;width:1200px;text-align:center;top:3486px;color:var(--white)}
.field{background:var(--white);font-size:14px;color:#444;padding:18px 12px}
.submit{left:503px;top:3837px;width:194px;height:51px;border:2px solid var(--white);color:var(--white);font-weight:700;font-size:16px;display:flex;align-items:center;justify-content:center}
/* footer */
.site-footer{top:3973px;left:0;width:1200px;height:381px;background:var(--night);color:var(--white)}
.footer-brand{left:112px;top:4042px;color:var(--white);font-size:30px}
.footer-social{left:148px;top:4118px;display:flex;gap:15px}
.footer-social span{width:29px;height:29px;display:block}
.footer-head{top:4045px;font-size:18px;font-weight:700;letter-spacing:.2px}
.footer-links{left:422px;top:4094px;list-style:none;font-size:14px;line-height:26.8px;color:#ddd}
.contact-row{left:582px;display:flex;gap:14px;font-size:14px;line-height:24px;color:#ddd;align-items:flex-start}
.contact-row .ico{width:34px;height:34px;background:var(--red);flex:none;display:flex;align-items:center;justify-content:center}
.footer-map{left:880px;top:4093px;width:210px;height:150px;background:linear-gradient(135deg,#dfe7d3,#e9ecef 50%,#cfdcea);border:3px solid #fff}
.copyright{left:0;width:1200px;top:4312px;text-align:center;font-size:14px;color:#ddd}
</style>
</head>
<body>

<header class="abs site-header">
  <div class="abs brand" style="left:112px;top:16px;font-size:38px"><span class="brand-square"></span>KLR Buildworks</div>
  <div class="abs header-phone">
    <span class="ico round"><svg width="22" height="22" viewBox="0 0 24 24"><path fill="#fff" d="M6.6 10.8a15.1 15.1 0 006.6 6.6l2.2-2.2c.3-.3.7-.4 1-.2 1.1.4 2.3.6 3.6.6.6 0 1 .4 1 1V20c0 .6-.4 1-1 1A17 17 0 013 4c0-.6.4-1 1-1h3.5c.6 0 1 .4 1 1 0 1.3.2 2.5.6 3.6.1.3 0 .7-.2 1z"/></svg></span>
    1 (555) 014-2278
  </div>
  <div class="abs header-divider"></div>
  <div class="abs header-social" aria-label="Social profiles">
    <span class="round"></span><span class="round"></span><span class="round"></span><span class="round"></span>
  </div>
</header>

<nav class="abs main-nav">
  <a class="current" style="left:112px">HOME</a>
  <a style="left:237px">COMPANY PROFILE</a>
  <a style="left:470px">SERVICES</a>
  <a style="left:627px">WHY CHOOSE US</a>
  <a style="left:838px">OUR WORKS</a>
  <a style="left:1009px">CONTACT</a>
</nav>

<section class="abs hero">
  <div class="hero-photo" role="img" aria-label="Operator driving a yellow cable plow with a red conduit reel on a green lawn"></div>
  <div class="hero-shade"></div>
  <h1 class="abs hero-title oswald"><b>KLR</b> BUILDWORKS</h1>
  <p class="abs hero-sub">At KLR Buildworks we strive to provide creative solutions,<br>on-time, on-budget and beyond expectations</p>
  <div class="abs btn-red hero-btn">GET STARTED</div>
  <div class="abs hero-scroll"></div>
  <svg class="abs" style="left:0;top:555px" width="1200" height="75" viewBox="0 0 1200 75"><polygon points="0,10 1200,42 1200,75 0,75" fill="#fff"/><polygon points="0,10 1200,42 1200,58 0,22" fill="var(--red)"/></svg>
</section>

<div class="abs about-photo" role="img" aria-label="Worker in orange safety gear operating a red directional drill rig"></div>
<h2 class="abs section-title about-title"><b>ABOUT</b> US</h2>
<div class="abs about-rule"></div>
<p class="abs about-text">KLR Buildworks is a safety conscious, productive &amp; efficient construction firm capable of all facets of civil construction. We have completed thousands of projects across Alberta, Saskatchewan and British Columbia working within various industry sectors. We have built a diverse team of skilled professionals who take a great deal of pride in their work and aim to achieve the highest levels of customer satisfaction.<br>Each of KLR's construction crews are dispatched with a full complement of late model equipment and tools required to complete civil underground construction projects in a safe and efficient manner meeting all criteria established</p>
<div class="abs btn-red about-btn">LEARN MORE</div>

<section class="abs why" role="img" aria-label="Dusk view of construction machinery on a job site"></section>
<h2 class="abs section-title why-title"><b>WHY CHOOSE</b> US</h2>
<div class="abs why-card" style="left:112px">
  <svg width="84" height="84" viewBox="0 0 84 84" fill="none" stroke="#fff" stroke-width="2.5"><circle cx="42" cy="20" r="8"/><circle cx="22" cy="28" r="6"/><circle cx="62" cy="28" r="6"/><path d="M28 50c0-10 6-16 14-16s14 6 14 16M10 52c0-8 5-13 12-13M74 52c0-8-5-13-12-13"/><path d="M18 62l14-6 10 6 10-6 14 6-24 12z"/></svg>
  <ul><li>Accredited health and safety program</li><li>Proven track record of safety excellence</li><li>Continuous training and development of employees</li></ul>
</div>
<div class="abs why-card" style="left:443px">
  <svg width="84" height="84" viewBox="0 0 84 84" fill="none" stroke="#fff" stroke-width="2.5"><path d="M30 30a12 12 0 0124 0M26 30h32"/><circle cx="34" cy="56" r="12"/><circle cx="34" cy="56" r="4"/><circle cx="58" cy="50" r="7"/><circle cx="58" cy="50" r="2.5"/></svg>
  <ul><li>Productive and efficient crews</li><li>Current fleet of modern equipment</li><li>Use of latest construction techniques /technologies</li></ul>
</div>
<div class="abs why-card" style="left:776px">
  <svg width="84" height="84" viewBox="0 0 84 84" fill="none" stroke="#fff" stroke-width="2.5"><circle cx="42" cy="42" r="36"/><circle cx="42" cy="42" r="26"/><path d="M30 42l9 9 16-17"/></svg>
  <ul><li>Quality and process driven</li><li>Excellent customer service</li><li>Privately owned and operated</li><li>Dependable, Reliable and Honest</li></ul>
</div>

<section class="abs reviews"></section>
<h2 class="abs section-title reviews-title"><b>WHAT PEOPLE</b> ARE SAYING...</h2>
<svg class="abs arrow" style="left:92px" width="16" height="26" viewBox="0 0 16 26"><path d="M13 2L3 13l10 11" stroke="#333" stroke-width="2" fill="none"/></svg>
<svg class="abs arrow" style="left:1092px" width="16" height="26" viewBox="0 0 16 26"><path d="M3 2l10 11L3 24" stroke="#333" stroke-width="2" fill="none"/></svg>
<div class="abs review-card" style="left:125px">
  <span class="quote">&ldquo;</span><span class="stars">★★★★★</span>
  <p>Sed ut perspiciatis unde e natus error sit voluptatem accusantium doloremque latium, totam rem aperiam, eaque ipsa quae ab illo in veritatis et quasi architecto beatae vitae dicta sunt explicabo.</p>
  <span class="tail"></span>
</div>
<div class="abs review-card" style="left:612px">
  <span class="quote">&ldquo;</span><span class="stars">★★★★★</span>
  <p>Sed ut perspiciatis unde e natus error sit voluptatem accusantium doloremque latium, totam rem aperiam, eaque ipsa quae ab illo in veritatis et quasi architecto beatae vitae dicta sunt explicabo.</p>
  <span class="tail"></span>
</div>
<div class="abs avatar round" style="left:125px" role="img" aria-label="Reviewer portrait"></div>
<div class="abs reviewer" style="left:204px">Daniel Prewitt<small>orem Ipsum passage</small></div>
<div class="abs avatar round" style="left:612px" role="img" aria-label="Reviewer portrait"></div>
<div class="abs reviewer" style="left:691px">Owen Lachance.<small>orem Ipsum passage</small></div>

<h2 class="abs section-title work-title"><b>OUR</b> WORK</h2>
<div class="abs work-tile" style="left:112px;top:2638px;background:linear-gradient(180deg,#9ea3a8,#7c8080 50%,#4f5b3c)" role="img" aria-label="Hydrovac truck working beside a roadway"></div>
<div class="abs work-tile" style="left:442px;top:2638px;background:linear-gradient(135deg,#3d5a2a,#c29a25 50%,#5a8a2e)" role="img" aria-label="Operator on a yellow cable plow"></div>
<div class="abs work-tile" style="left:773px;top:2638px;background:linear-gradient(135deg,#d9dde0,#f4f4f4 50%,#8a9097)" role="img" aria-label="White service truck with fibre equipment"></div>
<div class="abs work-tile" style="left:112px;top:2976px;background:linear-gradient(135deg,#6b7075,#3d8fc8 50%,#4a4f55)" role="img" aria-label="Blue pump equipment with pressure gauge"></div>
<div class="abs work-tile" style="left:442px;top:2976px;background:linear-gradient(160deg,#4f6b3a,#2a2a2a 45%,#5a3a2a)" role="img" aria-label="Directional drill rig among trees"></div>
<div class="abs work-tile" style="left:773px;top:2976px;background:linear-gradient(180deg,#8da5c0,#6e7d4a 40%,#b89a2e 70%,#5c6b35)" role="img" aria-label="Tracked plow laying conduit in a field"></div>

<section class="abs contact" role="img" aria-label="Red tinted background of a cable reel"></section>
<h2 class="abs section-title contact-title"><b>GET IN</b> TOUCH</h2>
<div class="abs field" style="left:205px;top:3575px;width:387px;height:50px">First Name</div>
<div class="abs field" style="left:607px;top:3575px;width:386px;height:50px">Last Name</div>
<div class="abs field" style="left:205px;top:3642px;width:387px;height:50px">Email</div>
<div class="abs field" style="left:607px;top:3642px;width:386px;height:50px">Phone</div>
<div class="abs field" style="left:205px;top:3710px;width:788px;height:105px">How Can We Help?</div>
<div class="abs submit">SUBMIT</div>

<footer class="abs site-footer"></footer>
<div class="abs brand footer-brand"><span class="brand-square"></span>KLR Buildworks</div>
<div class="abs footer-social" aria-label="Social profiles">
  <span class="round" style="background:#3b5a9a"></span><span class="round" style="background:#c2305a"></span><span class="round" style="background:#2a78b5"></span><span class="round" style="background:#2a3a8a"></span>
</div>
<div class="abs footer-head" style="left:422px">QUICK LINKS</div>
<ul class="abs footer-links"><li>Home</li><li>Company Profile</li><li>Services</li><li>Why Choose Us</li><li>Our Works</li><li>Contact</li></ul>
<div class="abs footer-head" style="left:582px">CONTACT DETAILS</div>
<div class="abs contact-row" style="top:4090px"><span class="ico round"><svg width="16" height="18" viewBox="0 0 24 24"><path fill="#fff" d="M12 2a7 7 0 00-7 7c0 5 7 13 7 13s7-8 7-13a7 7 0 00-7-7zm0 9.5A2.5 2.5 0 1112 6a2.5 2.5 0 010 5.5z"/></svg></span><span>18 Larkfield Ave<br>Maple Ridge, Ab T0x...</span></div>
<div class="abs contact-row" style="top:4163px"><span class="ico round"><svg width="16" height="16" viewBox="0 0 24 24"><path fill="#fff" d="M6.6 10.8a15.1 15.1 0 006.6 6.6l2.2-2.2c.3-.3.7-.4 1-.2 1.1.4 2.3.6 3.6.6.6 0 1 .4 1 1V20c0 .6-.4 1-1 1A17 17 0 013 4c0-.6.4-1 1-1h3.5c.6 0 1 .4 1 1 0 1.3.2 2.5.6 3.6.1.3 0 .7-.2 1z"/></svg></span><span style="padding-top:5px">1 (555) 014-2278</span></div>
<div class="abs contact-row" style="top:4217px"><span class="ico round"><svg width="16" height="14" viewBox="0 0 24 18"><path fill="#fff" d="M0 0h24v18H0z"/><path d="M1 1l11 9 11-9" stroke="var(--red)" stroke-width="2" fill="none"/></svg></span><span style="padding-top:5px">info@KLRBuildworks.com</span></div>
<div class="abs footer-head" style="left:880px">LOCATION MAP</div>
<div class="abs footer-map" role="img" aria-label="Street map showing the office location"></div>
<div class="abs copyright">© 2022 KLR Buildworks.All Rights Reserved</div>

</body>
</html>
```